7 page website for Dog Training Business

we are seeking a website design that should be 7 pages for a Las Vegas Dog training business. the site will have a heavy focus on video, and social media. Ideas design can be borrowed from http://velvetacre.net
attached is a copy of the logo and business card mock up. Content is currently being written and will be posted shortly

Training

```html
<!DOCTYPE html>
<html lang="en">
<head>
<meta charset="utf-8">
<title>Bravo Dog Training</title>
<link href="https://fonts.googleapis.com/css2?family=Kalam&family=Lato:wght@400;700&family=Open+Sans:wght@600;700&family=Raleway:wght@400;500&display=swap" rel="stylesheet">
<style>
:root{
  --red:#8b2813;
  --red-dark:#6e1e0d;
  --lime:#c3d548;
  --ink:#1d1d1d;
  --green-ink:#2e5530;
  --page:#ffffff;
  --outer:#eeeeee;
  --black:#000000;
}
*{box-sizing:border-box;margin:0;padding:0}
html,body{width:875px;height:1200px;overflow:hidden}
body{background:var(--outer);font-family:'Lato',sans-serif;color:var(--ink);position:relative}
.page{position:absolute;left:74px;top:0;width:731px;height:1038px;background:var(--page);box-shadow:0 0 10px rgba(0,0,0,.35)}
.abs{position:absolute}

.brand{left:90px;top:22px;display:flex;align-items:center;gap:6px}
.brand-dot{width:34px;height:34px;border-radius:50%;background:var(--lime)}
.brand-name{font-family:'Open Sans',sans-serif;font-weight:700;font-size:15px;color:var(--red);line-height:1.1;width:80px}
.tagline{left:240px;top:12px;width:360px;text-align:center;font-family:'Kalam',cursive;font-size:26px;line-height:33px;color:var(--green-ink)}
.social{display:flex;gap:7px}
.social span{width:22px;height:22px;border-radius:50%;background:var(--red)}
.social span:first-child{background:var(--lime)}
.social.head{left:676px;top:50px}

.ribbon{left:0;top:86px}
.nav{display:flex;gap:0;font-family:'Open Sans',sans-serif;font-weight:600;font-size:11.5px}
.nav a{color:#fff;text-decoration:none;margin-right:22px}
.nav a.active{color:var(--lime)}
.nav.top{left:95px;top:96px}

.hero{left:91px;top:122px;width:694px;height:260px;background:linear-gradient(90deg,#6f8f3e 0%,#b89070 35%,#8a6a4a 60%,#7a9445 100%)}
.hero-caption{left:91px;top:336px;width:694px;height:46px;background:rgba(139,40,19,.82);color:#fff;font-family:'Open Sans',sans-serif;font-weight:700;font-size:21px;padding:8px 8px;letter-spacing:-.3px}

.heading{display:flex;align-items:center;gap:4px;font-family:'Raleway',sans-serif;font-size:18px;color:var(--ink)}
.heading em{font-style:normal;color:var(--red)}
.heading .title{border-bottom:1px solid var(--red);padding-bottom:3px}
.heading.light{color:#fff}
.paw{width:26px;height:24px;flex:none}

.intro{left:94px;top:450px;width:336px;font-size:8.4px;line-height:13.7px}
.btn{display:inline-block;background:var(--red);color:#fff;font-size:8.5px;text-align:center}
.intro-btn{left:93px;top:518px;width:63px;height:21px;line-height:21px}

.quote{left:454px;top:452px;width:315px;font-size:8.4px;line-height:17.6px;text-indent:10px}
.qmark{font-family:'Open Sans',sans-serif;font-weight:700;font-size:16px}
.author{left:620px;top:538px;text-align:right;font-size:9.5px;line-height:14px;width:68px}
.author .role{color:var(--red)}
.avatar{left:694px;top:515px;width:66px;height:66px;border-radius:50%;background:linear-gradient(160deg,#a8421e,#c98a62);border:2px solid #fff;box-shadow:0 0 0 1px #ccc}

.card{top:610px;width:218px;height:213px;background:var(--red);border:2px solid var(--red-dark);text-align:center;color:#fff}
.card-photo{margin:16px auto 0;width:168px;height:91px}
.card h3{font-size:10px;font-weight:700;margin-top:13px}
.card p{font-size:8.4px;line-height:13.6px;margin:2px 12px 0}
.card .btn{background:var(--lime);color:var(--red);width:64px;height:19px;line-height:19px;margin-top:8px}

.arrows{left:740px;top:864px;display:flex;gap:7px}
.arrows span{width:20px;height:18px;display:flex;align-items:center;justify-content:center}
.thumb{top:888px;width:158px;height:115px}

.footer{left:0;top:1038px;width:875px;height:146px;background:var(--black);color:#fff}
.strip{left:0;top:1184px;width:875px;height:16px;background:var(--red)}
.contact-line{left:118px;top:1088px;display:flex;align-items:center;gap:8px;font-size:10px;color:#fff}
.contact-line .item{display:flex;align-items:center;gap:6px;margin-right:6px}
.rule{left:91px;top:1128px;width:694px;height:1px;background:#333}
.social.foot{left:676px;top:1087px}
.social.foot span{background:var(--red)}
</style>
</head>
<body>
<svg width="0" height="0" style="position:absolute">
  <defs>
    <symbol id="paw" viewBox="0 0 26 24">
      <ellipse cx="13" cy="16" rx="6.5" ry="5.5"/>
      <ellipse cx="4" cy="10" rx="2.6" ry="3.3"/>
      <ellipse cx="9" cy="5" rx="2.6" ry="3.5"/>
      <ellipse cx="17" cy="5" rx="2.6" ry="3.5"/>
      <ellipse cx="22" cy="10" rx="2.6" ry="3.3"/>
    </symbol>
  </defs>
</svg>

<div class="page"></div>

<header>
  <div class="abs brand"><span class="brand-dot"></span><span class="brand-name">Bravo Dog Training</span></div>
  <p class="abs tagline">Professional dog training services for you!</p>
  <div class="abs social head" aria-label="Social links"><span></span><span></span><span></span><span></span></div>

  <svg class="abs ribbon" width="875" height="52" viewBox="0 0 875 52">
    <polygon points="4,28 18,14 74,14 74,46 18,46 16,42" fill="var(--red-dark)"/>
    <polygon points="871,28 858,14 806,14 806,46 858,46 860,42" fill="var(--red-dark)"/>
    <polygon points="62,46 74,46 74,52" fill="#4a1508"/>
    <polygon points="813,46 806,46 806,52" fill="#4a1508"/>
    <rect x="46" y="2" width="784" height="36" fill="var(--red)"/>
    <rect x="51" y="6" width="774" height="28" fill="none" stroke="var(--red-dark)" stroke-width="1"/>
  </svg>
  <nav class="abs nav top">
    <a class="active">Home</a><a>About Us</a><a>Services</a><a>Photos/Videos</a><a>FAQ</a><a>Tips</a><a>Store</a><a>Contacts</a>
  </nav>
</header>

<div class="abs hero" role="img" aria-label="Photo of a smiling woman with a small terrier on a lawn"></div>
<div class="abs hero-caption">Everything You Need To get Started Right Away !</div>

<section>
  <h2 class="abs heading" style="left:94px;top:404px"><svg class="paw" fill="var(--red)"><use href="#paw"/></svg><span class="title">Welcome To <em>Bravo Dog Training</em></span></h2>
  <p class="abs intro">Duis autem vel eum iriure dolor in hendrerit in vulputate velit esse molestie consequat, vel illum dolore eu feugiat nulla facilisis at vero eros et accumsan et iusto odio dignissim qui blandit praesent luptatum zzril delenit augue duis dolore te feugait nulla facilisi.feugiat nulla facilisis at vero eros et accumsan et iusto .</p>
  <span class="abs btn intro-btn">Read More</span>
</section>

<section>
  <h2 class="abs heading" style="left:450px;top:404px"><svg class="paw" fill="var(--red)"><use href="#paw"/></svg><span class="title">What People <em>Say About Us</em></span></h2>
  <span class="abs qmark" style="left:453px;top:432px">“</span>
  <p class="abs quote">Duis autem vel eum iriure dolor in hendrerit in vulputate velit esse molestie consequat, vel illum dolore eu feugiat nulla facilisis at vero eros et accumsan et iusto odio dignissim qui blandit praesent luptatum zzril delenit</p>
  <span class="abs qmark" style="left:682px;top:496px">”</span>
  <div class="abs author">Mr.Orlen<br><span class="role">Director</span></div>
  <div class="abs avatar" role="img" aria-label="Portrait of the director"></div>
</section>

<section>
  <h2 class="abs heading" style="left:94px;top:567px"><svg class="paw" fill="var(--red)"><use href="#paw"/></svg><span class="title">Our <em>Services</em></span></h2>
  <div class="abs card" style="left:91px">
    <div class="card-photo" role="img" aria-label="Child and woman with a golden retriever" style="background:linear-gradient(90deg,#9a8a70,#e8e2d8,#7a5a40)"></div>
    <h3>IN-HOME TRAINING</h3>
    <p>putate velit esse molestie consequat, vel illum dolore eu feugiat nulla facilisis at vero eros et accumsan et iusto</p>
    <span class="btn">Read More</span>
  </div>
  <div class="abs card" style="left:329px">
    <div class="card-photo" role="img" aria-label="Dog holding a ball on a green field" style="background:linear-gradient(180deg,#3e5a3a,#4c7a3a 60%,#5a8f3c)"></div>
    <h3>BOARD-AND-TRAIN PACKAGES</h3>
    <p>putate velit esse molestie consequat, vel illum dolore eu feugiat nulla facilisis at vero eros et accumsan et iusto</p>
    <span class="btn">Read More</span>
  </div>
  <div class="abs card" style="left:566px">
    <div class="card-photo" role="img" aria-label="Dog jumping an agility hurdle" style="background:linear-gradient(180deg,#3e7ac2,#6a8c5a 65%,#5a7e3a)"></div>
    <h3>PHONE CONSULTATION TRAINING</h3>
    <p>putate velit esse molestie consequat, vel illum dolore eu feugiat nulla facilisis at vero eros et accumsan et iusto</p>
    <span class="btn">Read More</span>
  </div>
</section>

<section>
  <h2 class="abs heading" style="left:94px;top:842px"><svg class="paw" fill="var(--red)"><use href="#paw"/></svg><span class="title">Our <em>Gallery</em></span></h2>
  <div class="abs arrows">
    <span style="background:var(--red)"><svg width="10" height="10" viewBox="0 0 10 10" fill="none" stroke="#fff" stroke-width="1.5"><path d="M5 1 1 5l4 4M9 1 5 5l4 4"/></svg></span>
    <span style="background:#000"><svg width="10" height="10" viewBox="0 0 10 10" fill="none" stroke="#fff" stroke-width="1.5"><path d="M1 1l4 4-4 4M5 1l4 4-4 4"/></svg></span>
  </div>
  <div class="abs thumb" style="left:91px;background:linear-gradient(135deg,#a8553a,#b8694a)" role="img" aria-label="Puppy playing with a red ball">
    <svg width="158" height="115" style="position:absolute;left:0;top:0">
      <circle cx="60" cy="57" r="12" fill="#f3e6e0"/><circle cx="59" cy="56" r="4" fill="none" stroke="var(--red)" stroke-width="1.6"/><path d="M62 59l3 3" stroke="var(--red)" stroke-width="1.6"/>
      <circle cx="92" cy="57" r="12" fill="var(--red)"/><path d="M88 59l8-5" stroke="#fff" stroke-width="1.6"/>
    </svg>
  </div>
  <div class="abs thumb" style="left:269px;background:linear-gradient(180deg,#6a7a5a,#9aa080 50%,#6c8a3c)" role="img" aria-label="Dog leaping through an agility tire"></div>
  <div class="abs thumb" style="left:446px;background:linear-gradient(180deg,#c8ccd0,#a8b0b4 60%,#5a6a3a)" role="img" aria-label="Trainer and shepherd dog jumping a hurdle"></div>
  <div class="abs thumb" style="left:625px;background:linear-gradient(90deg,#c9a58a,#3a3030 50%,#d8b8a0)" role="img" aria-label="Couple hugging a mountain dog"></div>
</section>

<footer>
  <div class="abs footer"></div>
  <h2 class="abs heading light" style="left:94px;top:1050px"><svg class="paw" fill="#fff"><use href="#paw"/></svg><span>Contact <em>Us</em></span></h2>
  <h2 class="abs heading light" style="left:630px;top:1050px"><svg class="paw" fill="#fff"><use href="#paw"/></svg><span>Stay <em>Connected</em></span></h2>
  <div class="abs contact-line">
    <span class="item"><svg width="10" height="14" viewBox="0 0 10 14"><path d="M5 0a5 5 0 0 1 5 5c0 3.5-5 9-5 9S0 8.5 0 5a5 5 0 0 1 5-5z" fill="var(--red)"/><circle cx="5" cy="5" r="1.8" fill="#000"/></svg>4127 Larkspur Lane Reno, NV 89502</span>
    <span class="item"><svg width="12" height="12" viewBox="0 0 12 12"><path d="M2 0l3 3-1.5 1.5a7 7 0 0 0 4 4L9 7l3 3-2 2C5 12 0 7 0 2z" fill="var(--red)"/></svg>+1 800 555 0142</span>
    <span class="item"><svg width="14" height="10" viewBox="0 0 14 10"><rect width="14" height="10" fill="var(--red)"/><path d="M0 0l7 5 7-5" fill="none" stroke="#000" stroke-width="1"/></svg>E-mail: hello@bravodogs.example</span>
  </div>
  <div class="abs social foot" aria-label="Social links"><span></span><span></span><span></span><span></span></div>
  <div class="abs rule"></div>
  <nav class="abs nav" style="left:95px;top:1146px">
    <a class="active">Home</a><a>About Us</a><a>Services</a><a>Photos/Videos</a><a>FAQ</a><a>Tips</a><a>Store</a><a>Contacts</a>
  </nav>
  <div class="abs strip"></div>
</footer>
</body>
</html>
```